Stationery for Villa Marenta Design Hotel**

Who we are:

Wander on an isolated beach while breathing in the fresh, salty, sea air. Listen to the warm Pacific wind rustling through green palm trees as you walk to a pristine lagoon. Feel the delicious warmth of the sun kiss your skin; the beach is yours. At Villa Marenta you can experience a vacation in undisturbed, natural beauty. We have created a place for you to find new strength, relaxation, and inner harmony. We offer total rest to the experienced traveler from all over the world.

We are a brand new and smartly built design-hotel (under construction) close to a unique beach and a fantastic surf spot in Huatulco, Southwest Mexico.

As you can see in the attachments, we do have an established corporate design, but as for now still need a format for booklets for information around our hotel and things to do in the area, important numbers (we fill in the content for that one).

Our corporate colors:
green #64b445, brown #b07043, blue #0ab7cf, yellow # f9b02a and #fcc01a, navy #444f69
Corporate fonts:
Krub and Miller Banner.
For further information access:
www.villamarenta.example
https://slidevault.example/view/QmPxLwZrTyKsNbVcHdJe/

Social Media: VillaMarenta

Industry/Entity Type

Hotel

Font styles to use
Other font styles liked:
• Krub, Miller Banner

Requirements
Must have
• Stick to Logo Design, defined corporate elements, logo, colors, fonts and general touch and feel
Nice to have
• Who we are:

Our corporate colors:
Corporate fonts:
Krub and Miller Banner.
www.villamarenta.example

Social Media: VillaMarenta

```html
<!DOCTYPE html>
<html lang="en">
<head>
<meta charset="utf-8">
<title>Villa Marenta Design Hotel – Letterhead</title>
<link rel="stylesheet" href="https://fonts.googleapis.com/css2?family=Krub:wght@400;500&family=Tinos&display=swap">
<style>
  :root {
    --backdrop: #d9dddf;
    --paper: #ffffff;
    --gold: #f0a81e;
    --gold-deep: #e39a14;
    --leaf-wash: #dfeccc;
    --leaf-wash-soft: #eef5e3;
    --ink: #4a4a4a;
    --icon: #ffffff;
  }
  * { box-sizing: border-box; margin: 0; padding: 0; }
  html, body { width: 1200px; height: 784px; overflow: hidden; }
  body {
    background: var(--backdrop);
    display: flex;
    align-items: center;
    justify-content: center;
  }
  .letterhead {
    position: relative;
    width: 523px;
    height: 740px;
    background: var(--paper);
    box-shadow: 0 6px 18px rgba(0,0,0,0.12);
    overflow: hidden;
  }
  .side-rule {
    position: absolute;
    left: 14px;
    top: 0;
    width: 14px;
    height: 100%;
    background: linear-gradient(to right, var(--gold), var(--gold-deep));
  }
  .brand {
    position: absolute;
    left: 44px;
    top: 40px;
    display: flex;
    align-items: center;
    gap: 10px;
  }
  .brand-mark {
    width: 14px;
    height: 14px;
    background: var(--gold);
  }
  .brand-name {
    font-family: "Krub", sans-serif;
    font-weight: 500;
    font-size: 22px;
    letter-spacing: 2px;
    color: var(--gold);
    text-transform: uppercase;
  }
  .brand-tagline {
    position: absolute;
    left: 68px;
    top: 72px;
    font-family: "Krub", sans-serif;
    font-size: 7px;
    letter-spacing: 2px;
    color: var(--gold);
    text-transform: uppercase;
  }
  .contact {
    position: absolute;
    left: 12px;
    bottom: 40px;
    list-style: none;
  }
  .contact li {
    display: flex;
    align-items: flex-start;
    gap: 10px;
    font-family: "Tinos", serif;
    font-size: 11px;
    line-height: 14px;
    color: var(--ink);
    margin-bottom: 3px;
  }
  .contact-icon {
    flex: none;
    width: 18px;
    height: 14px;
    display: flex;
    align-items: center;
    justify-content: center;
  }
  .leaf-wash {
    position: absolute;
    right: -40px;
    bottom: -30px;
    width: 300px;
    height: 310px;
    border-radius: 50% 45% 40% 55%;
    background: radial-gradient(circle at 45% 45%, var(--leaf-wash), var(--leaf-wash-soft) 70%, rgba(255,255,255,0) 100%);
  }
</style>
</head>
<body>
  <main class="letterhead">
    <div class="side-rule"></div>

    <div class="brand">
      <span class="brand-mark"></span>
      <span class="brand-name">Villa Marenta</span>
    </div>
    <p class="brand-tagline">Playa Serena · Design Hotel</p>

    <div class="leaf-wash" role="img" aria-label="Faint watercolour monstera leaf in soft green"></div>

    <ul class="contact">
      <li>
        <span class="contact-icon">
          <svg width="10" height="12" viewBox="0 0 10 12"><path d="M5 1a3.5 3.5 0 0 0-3.5 3.5C1.5 7 5 11 5 11s3.5-4 3.5-6.5A3.5 3.5 0 0 0 5 1z" fill="none" stroke="var(--icon)" stroke-width="1.2"/><circle cx="5" cy="4.5" r="1.1" fill="var(--icon)"/></svg>
        </span>
        <span>Villa Marenta, Playa Serena,<br>Puerto Lirio, Costa Sur</span>
      </li>
      <li>
        <span class="contact-icon">
          <svg width="10" height="10" viewBox="0 0 10 10"><path d="M2.2 1.2l1.6 1.9-.9 1.1a5.5 5.5 0 0 0 2.9 2.9l1.1-.9 1.9 1.6-.9 1.1C5 8.8 1.2 5 1.1 2.1z" fill="var(--icon)"/></svg>
        </span>
        <span>+52 (000) 555 0142</span>
      </li>
      <li>
        <span class="contact-icon">
          <svg width="11" height="9" viewBox="0 0 11 9"><rect x="0.7" y="0.7" width="9.6" height="7.6" fill="none" stroke="var(--icon)" stroke-width="1.1"/><path d="M0.9 1l4.6 4 4.6-4" fill="none" stroke="var(--icon)" stroke-width="1.1"/></svg>
        </span>
        <span>hello@villamarenta.example</span>
      </li>
      <li>
        <span class="contact-icon">
          <svg width="10" height="10" viewBox="0 0 10 10"><circle cx="5" cy="5" r="4.2" fill="none" stroke="var(--icon)" stroke-width="1"/><ellipse cx="5" cy="5" rx="1.8" ry="4.2" fill="none" stroke="var(--icon)" stroke-width="0.9"/><path d="M0.8 5h8.4" stroke="var(--icon)" stroke-width="0.9"/></svg>
        </span>
        <span>www.villamarenta.example</span>
      </li>
    </ul>
  </main>
</body>
</html>
```